New Innovative Counselling and psychotherapy Service needs Business Card design

Keep it simple and professional. On one side, just company name and logo (perhaps in all blue) and maybe a tag line.

On other side (all white) my name and Qualifications in centre

Industry/Entity Type

Health And Wellness

Contact Information for Business Card

Dara Whelby
Counsellor & Psychotherapist
BSc (Psychol.), BA, Dip. (Couns. & Psych.), PG.Cert (CBT), FGTrK, ONRE

I will also require Mobile no, Email and web site address of which I'll pass on to final designer.

Font styles to use
Sans Serif

Requirements
Must have
• My Logo Only and please use the colours in logo that is in it.
Should not have
• Any other images

```html
<!DOCTYPE html>
<html lang="en">
<head>
<meta charset="utf-8">
<title>Willowmere Lane – Business Card</title>
<link rel="stylesheet" href="https://fonts.googleapis.com/css2?family=Montserrat:wght@400&family=Roboto:wght@400;700&display=swap">
<style>
  :root {
    --backdrop: #3b3b3b;
    --card: #242424;
    --emboss: #4a4a4a;
    --blue: #3cb0ea;
    --green: #7bc144;
    --white: #ffffff;
    --muted: #e6e6e6;
  }
  * { margin: 0; padding: 0; box-sizing: border-box; }
  html, body { width: 799px; height: 1200px; overflow: hidden; }
  body {
    background: var(--backdrop);
    font-family: "Roboto", Arial, sans-serif;
    position: relative;
  }
  .card {
    position: absolute;
    left: 60px;
    width: 679px;
    height: 390px;
    background: var(--card);
    border-radius: 26px;
    overflow: hidden;
    box-shadow: 0 10px 24px rgba(0,0,0,0.45);
  }
  .card--front { top: 120px; }
  .card--back { top: 690px; }

  /* front */
  .front-mark {
    position: absolute;
    inset: 0;
    display: flex;
    align-items: center;
    justify-content: center;
    gap: 18px;
  }
  .front-mark__dot {
    width: 46px; height: 46px; border-radius: 50%;
    background: var(--emboss);
  }
  .front-mark__name {
    font-family: "Montserrat", Arial, sans-serif;
    font-weight: 400;
    font-size: 44px;
    color: var(--emboss);
  }

  /* back */
  .band {
    position: absolute; left: 0; top: 0; bottom: 0;
    width: 62px; background: var(--blue);
    border-right: 5px solid var(--green);
  }
  .brand {
    position: absolute; left: 100px; top: 52px;
    display: flex; align-items: center; gap: 22px;
  }
  .brand__dot {
    width: 58px; height: 58px; border-radius: 50%;
    background: var(--blue);
  }
  .brand__name {
    font-family: "Montserrat", Arial, sans-serif;
    font-weight: 400; font-size: 46px; color: var(--white);
  }
  .person { position: absolute; left: 100px; top: 150px; }
  .person__name {
    font-weight: 700; font-size: 26px; color: var(--blue); line-height: 1.1;
  }
  .person__role, .person__quals {
    font-size: 15px; color: var(--muted); line-height: 1.3;
  }
  .contact {
    position: absolute; left: 100px; top: 268px;
    list-style: none;
  }
  .contact__item {
    display: flex; align-items: center; gap: 14px;
    font-size: 17px; color: var(--white); line-height: 1.45;
  }
  .contact__icon { width: 14px; height: 14px; flex: none; }
</style>
</head>
<body>
  <section class="card card--front" aria-label="Card front">
    <div class="front-mark">
      <span class="front-mark__dot"></span>
      <span class="front-mark__name">Willowmere Lane</span>
    </div>
  </section>

  <section class="card card--back" aria-label="Card back">
    <div class="band"></div>
    <div class="brand">
      <span class="brand__dot"></span>
      <span class="brand__name">Willowmere Lane</span>
    </div>
    <div class="person">
      <p class="person__name">Dara Whelby</p>
      <p class="person__role">Counsellor &amp; Psychotherapist</p>
      <p class="person__quals">BSc (Psychol.), BA, Dip. (Couns. &amp; Psych.),<br>PG.Cert (CBT), FGTrK, ONRE</p>
    </div>
    <ul class="contact">
      <li class="contact__item">
        <svg class="contact__icon" viewBox="0 0 14 14"><path fill="#3cb0ea" d="M1 4c0-2 2-3 6-3s6 1 6 3v1h-3V4H4v1H1zM3 6h8l2 7H1z"/></svg>
        0865 318 4420
      </li>
      <li class="contact__item">
        <svg class="contact__icon" viewBox="0 0 14 14"><rect x="1" y="3" width="12" height="8" fill="#7bc144"/><path d="M1 3l6 5 6-5" stroke="#242424" stroke-width="1.2" fill="none"/></svg>
        dara.w@WillowmereLane.com
      </li>
      <li class="contact__item">
        <svg class="contact__icon" viewBox="0 0 14 14"><circle cx="7" cy="7" r="6" fill="#3cb0ea"/><path d="M1 7h12M7 1c-3 3-3 9 0 12M7 1c3 3 3 9 0 12" stroke="#242424" stroke-width="1" fill="none"/></svg>
        www.WillowmereLane.com
      </li>
    </ul>
  </section>
</body>
</html>
```